Outdoor Real Estate Sales Banner

It should say

248 Wexcombe Street, East Boston
Coming Spring 2026
3 Luxury Condos
Experience refined living with elegant design and high-end finishes. Thoughtfully crafted for both comfort and sophistication.
Construction by V Construction
Now Accepting Reservations

Schedule Your Private Tour Today
Marisol Thibault, Fenwick Realty | 617-555-0142 | Marisol@fenwickharbor.com
Gregory Hale, Fenwick Realty | 617-555-0187 | Gregory@fenwickharbor.com

Target Market(s)

30-45

Industry/Entity Type

real estate

Font styles to use
Serif

Requirements
Must have
• Colors of logo and preppy rich look
Nice to have
• herringbone incorporated the pattern
Should not have
• any loud colors

```html
<!DOCTYPE html>
<html lang="en">
<head>
<meta charset="utf-8">
<title>248 Wexcombe Street – Sales Banner</title>
<link href="https://fonts.googleapis.com/css2?family=Cinzel:wght@500;600;700&family=Jost:wght@300;400&display=swap" rel="stylesheet">
<style>
  :root {
    --page: #e8e5de;
    --navy: #1f2a40;
    --navy-deep: #18213a;
    --gold: #c9a966;
    --gold-soft: #b89a5c;
    --cream: #e6dcc4;
    --leaf: #7f955a;
    --leaf-dark: #3f5232;
    --skin-warm: #b89774;
  }
  * { margin: 0; padding: 0; box-sizing: border-box; }
  html, body { width: 1200px; height: 900px; overflow: hidden; background: var(--page); }
  .banner {
    position: absolute; left: 20px; top: 156px; width: 1160px; height: 588px;
    background: radial-gradient(ellipse at 50% 45%, #25314b 0%, var(--navy) 55%, var(--navy-deep) 100%);
    overflow: hidden; color: var(--gold);
  }
  .banner > * { position: absolute; }
  .rule { height: 2px; background: var(--gold); }
  .rule.thin { height: 1px; background: var(--gold-soft); }
  .center-text { left: 0; width: 100%; text-align: center; line-height: 1; white-space: nowrap; }
  .serif { font-family: "Cinzel", serif; font-weight: 700; }
  .sans { font-family: "Jost", sans-serif; }
  .address { top: 36px; font-size: 41px; letter-spacing: 0.5px; }
  .coming { top: 81px; font-size: 25px; font-weight: 400; color: var(--gold); }
  .headline { top: 113px; font-size: 64px; }
  .dot { width: 8px; height: 8px; border-radius: 50%; background: var(--gold); left: 576px; top: 187px; }
  .body-copy { font-size: 18px; font-weight: 300; color: var(--cream); }
  .body-copy.one { top: 201px; }
  .body-copy.two { top: 229px; }
  .builder { top: 262px; font-size: 25px; font-weight: 400; color: var(--cream); }
  .reserve { top: 306px; font-size: 33px; }
  .tour { top: 345px; font-size: 21px; font-weight: 400; color: var(--cream); }
  .portrait { top: 112px; height: 332px; }
  .portrait.left {
    left: 0; width: 290px;
    background: radial-gradient(ellipse 70% 80% at 45% 55%, var(--skin-warm) 0%, var(--leaf) 45%, var(--leaf-dark) 70%, rgba(31,42,64,0) 100%);
  }
  .portrait.right {
    left: 930px; width: 230px;
    background: radial-gradient(ellipse 75% 80% at 60% 55%, var(--skin-warm) 0%, var(--leaf) 45%, var(--leaf-dark) 70%, rgba(31,42,64,0) 100%);
  }
  .agent { line-height: 1; white-space: nowrap; }
  .agent.left { left: 30px; text-align: left; }
  .agent.right { right: 30px; text-align: right; }
  .agent-block { top: 462px; }
  .agent-name { font-family: "Cinzel", serif; font-weight: 700; font-size: 21px; display: block; }
  .agent-firm { font-family: "Cinzel", serif; font-weight: 700; font-size: 16px; display: block; margin-top: 7px; }
  .agent-phone { font-family: "Cinzel", serif; font-weight: 700; font-size: 35px; display: block; margin-top: 9px; }
  .agent-email { font-family: "Jost", sans-serif; font-weight: 400; font-size: 13px; letter-spacing: 1px; color: var(--cream); display: block; margin-top: 7px; }
  .firm-name { top: 505px; font-family: "Cinzel", serif; font-weight: 700; font-size: 36px; color: var(--gold); }
</style>
</head>
<body>
<section class="banner" aria-label="248 Wexcombe Street sales banner">
  <div class="rule" style="left:0;top:22px;width:1160px;"></div>

  <h1 class="center-text serif address">248 Wexcombe Street, East Boston</h1>

  <div class="rule thin" style="left:175px;top:93px;width:240px;"></div>
  <p class="center-text sans coming">COMING SPRING 2026</p>
  <div class="rule thin" style="left:745px;top:93px;width:240px;"></div>

  <h2 class="center-text serif headline">3 Luxury Condos</h2>
  <div class="rule thin" style="left:275px;top:190px;width:630px;"></div>
  <div class="dot"></div>

  <p class="center-text sans body-copy one">Experience refined living with elegant design and high-end finishes.</p>
  <p class="center-text sans body-copy two">Thoughtfully crafted for both comfort and sophistication.</p>
  <p class="center-text sans builder">Construction by V Construction</p>

  <div class="rule thin" style="left:295px;top:297px;width:570px;"></div>
  <h3 class="center-text serif reserve">Now Accepting Reservations</h3>
  <p class="center-text sans tour">Schedule Your Private Tour Today</p>
  <div class="rule thin" style="left:295px;top:377px;width:570px;"></div>

  <div class="portrait left" role="img" aria-label="Portrait photo of agent Marisol Thibault against a leafy street"></div>
  <div class="portrait right" role="img" aria-label="Portrait photo of agent Gregory Hale against a leafy street"></div>

  <div class="rule" style="left:0;top:443px;width:1160px;"></div>

  <div class="agent left agent-block">
    <span class="agent-name">Marisol Thibault</span>
    <span class="agent-firm">Fenwick Realty</span>
    <span class="agent-phone">617-555-0142</span>
    <span class="agent-email">Marisol@fenwickharbor.com</span>
  </div>

  <p class="center-text firm-name">Fenwick Realty</p>

  <div class="agent right agent-block">
    <span class="agent-name">Gregory Hale</span>
    <span class="agent-firm">Fenwick Realty</span>
    <span class="agent-phone">617-555-0187</span>
    <span class="agent-email">Gregory@fenwickharbor.com</span>
  </div>
</section>
</body>
</html>
```